Pediatric Therapy Clinic Brochure

We need a Brochure for a new pediatric therapy clinic. The clinic offers occupational therapy, physical therapy, speech therapy and feeding therapy. We want a brochure for parents, doctors and medical professional. It should have a fun and inviting, but still professional feel. Should be kid focused, bright and colorful. All the text / wording is there and a rough layout. Now I need someone to tidy and jazz it up and make it look professional.

Target Market(s)

Parents, doctors, medical professional

Industry/Entity Type

Medical

Font styles to use
Serif
Sans Serif

Requirements
Must have
• Keep All the text with information about services the same. Logo on front. Pictures throughout (use any of the pictures provided) (try and match up with corresponding service) (pictures are labeled). Need to have Map and contact info
• Keep colors consistent with our logo
Nice to have
• Background, special effects. Make it look fancy and professional
Should not have
• Not so busy that is takes away from the text

```html
<!DOCTYPE html>
<html lang="en">
<head>
<meta charset="utf-8">
<title>Pediatric Therapy Brochure – Inside Spread</title>
<link href="https://fonts.googleapis.com/css2?family=Bebas+Neue&family=Arimo:ital,wght@0,400;0,700;1,700&display=swap" rel="stylesheet">
<style>
  :root {
    --navy: #232852;
    --navy-deep: #1b1f44;
    --orange: #ee8a1c;
    --orange-dark: #d8700f;
    --lime: #c9dc2b;
    --rule-blue: #1f6fc4;
    --white: #ffffff;
    --stage: #9c9c9c;
  }
  * { box-sizing: border-box; margin: 0; padding: 0; }
  html, body { width: 1200px; height: 1200px; overflow: hidden; }
  body { background: var(--stage); position: relative; font-family: "Arimo", Arial, sans-serif; }

  .spread {
    position: absolute; left: 0; top: 135px; width: 1200px; height: 930px;
    background: linear-gradient(135deg, var(--navy) 0%, var(--navy-deep) 100%);
    display: flex; overflow: hidden;
  }
  .panel { position: relative; width: 400px; height: 100%; }
  .panel + .panel { border-left: 1px solid rgba(0,0,0,.25); }
  .decor { position: absolute; inset: 0; width: 100%; height: 100%; pointer-events: none; }

  .photo {
    position: absolute; border: 9px solid var(--orange); border-radius: 22px;
    box-shadow: 0 4px 10px rgba(0,0,0,.35);
  }
  .photo--paint { left: 30px; top: 28px; width: 340px; height: 210px;
    background: linear-gradient(135deg, #f4f2ef, #e9c9b3 55%, #d84a3a); }
  .photo--friends { left: 40px; top: 760px; width: 335px; height: 150px;
    background: linear-gradient(135deg, #e7d6c8, #c79a7a 50%, #8c6a58); }
  .photo--ball { left: 40px; top: 772px; width: 330px; height: 136px;
    background: linear-gradient(135deg, #f5f5f5, #9ac850 45%, #e6407a 75%, #f2f2f2); }

  .service { position: absolute; left: 30px; right: 25px; }
  .service__title {
    font-family: "Bebas Neue", "Oswald", sans-serif; color: var(--white);
    font-size: 38px; letter-spacing: .5px; text-align: center; line-height: 1;
  }
  .service__lead {
    color: var(--white); font-size: 13.5px; text-align: center; line-height: 1.3;
    margin-top: 6px; padding: 0 10px;
  }
  .service__rule { display: block; width: 100%; height: 14px; margin: 8px 0 10px; }
  .service__list { list-style: none; color: var(--lime); font-weight: 700; font-size: 15px; line-height: 1.32; }
  .service__list li { padding-left: 16px; position: relative; }
  .service__list li::before { content: "•"; position: absolute; left: 2px; }

  .service--ot { top: 262px; }
  .service--ot .service__list { font-size: 16px; line-height: 1.38; }

  .panel--middle .service { left: 22px; right: 18px; }
  .panel--middle .service__list { font-size: 14px; line-height: 1.3; }
  .panel--middle .service__lead { font-size: 13px; }
  .service--speech { top: 28px; }
  .service--sensory { top: 362px; }

  .service--feeding { top: 28px; }
  .service--physical { top: 288px; }
  .service--group { top: 598px; }

  .note {
    position: absolute; right: 22px; bottom: 92px; width: 200px;
    color: var(--white); font-size: 15px; text-align: center; line-height: 1.2;
  }
</style>
</head>
<body>
  <main class="spread">
    <section class="panel panel--left">
      <svg class="decor" viewBox="0 0 400 930" aria-hidden="true">
        <path d="M0 0 H150 C90 40 40 90 0 160 Z" fill="var(--orange)"/>
      </svg>
      <div class="photo photo--paint" role="img" aria-label="Smiling child showing hands covered in colourful finger paint"></div>
      <div class="service service--ot">
        <h2 class="service__title">Occupational Therapy</h2>
        <p class="service__lead">Helping children build better self-esteem, confidence and independence in all the things they do.</p>
        <svg class="service__rule" viewBox="0 0 345 14" preserveAspectRatio="none" aria-hidden="true"><path d="M0 12 Q170 -4 345 8" stroke="var(--rule-blue)" stroke-width="4" fill="none"/></svg>
        <ul class="service__list">
          <li>Sensory Processing Disorder</li>
          <li>Balance, Coordination, Strength, and Endurance</li>
          <li>Fine Motor and Handwriting</li>
          <li>Visual- Motor Integration</li>
          <li>Play and Social Skills</li>
          <li>Feeding and Oral Motor Skills</li>
          <li>Self-Care</li>
          <li>Academic and Cognitive Skills</li>
          <li>Behavioral Difficulties</li>
          <li>Developmental Delays</li>
        </ul>
      </div>
      <div class="photo photo--friends" role="img" aria-label="Three young children whispering and smiling together"></div>
    </section>

    <section class="panel panel--middle">
      <div class="service service--speech">
        <h2 class="service__title">Speech Therapy</h2>
        <p class="service__lead">Helping children speak, communicate and understand language.</p>
        <svg class="service__rule" viewBox="0 0 345 14" preserveAspectRatio="none" aria-hidden="true"><path d="M0 12 Q170 -4 345 8" stroke="var(--rule-blue)" stroke-width="4" fill="none"/></svg>
        <ul class="service__list">
          <li>Expressive and Receptive Language</li>
          <li>Speech and Language Developmental Milestones</li>
          <li>Articulation / Intelligibility</li>
          <li>Speech Fluency</li>
          <li>Pragmatics and Social Skills</li>
          <li>Literacy and Vocabulary</li>
          <li>Apraxia of Speech</li>
          <li>Augmentative and Alternative Communication</li>
          <li>Feeding and Oral Motor</li>
        </ul>
      </div>
      <div class="service service--sensory">
        <h2 class="service__title">Sensory Integration</h2>
        <p class="service__lead">Gradually increasing play based activities to improve a child's nervous system. Helping children learn to self-regulate their emotions, behaviors and arousal levels.</p>
        <svg class="service__rule" viewBox="0 0 345 14" preserveAspectRatio="none" aria-hidden="true"><path d="M0 12 Q170 -4 345 8" stroke="var(--rule-blue)" stroke-width="4" fill="none"/></svg>
        <ul class="service__list">
          <li>Autism and ADHD</li>
          <li>Sensory Processing Disorder</li>
          <li>Poor Tolerance of Sensory Stimuli from the Environment</li>
          <li>Meltdowns and Tantrums</li>
          <li>Poor Balance/Body Awareness</li>
          <li>Poor Attention and Concentration</li>
          <li>Poor Self-Regulation</li>
          <li>Behavior and Social Difficulties</li>
          <li>Poor Motor Coordination and Motor Planning</li>
          <li>Aggression, Frustration or Avoidance Behaviors</li>
        </ul>
      </div>
      <div class="photo photo--ball" role="img" aria-label="Child stretching backwards over a pink therapy ball"></div>
    </section>

    <section class="panel panel--right">
      <svg class="decor" viewBox="0 0 400 930" aria-hidden="true">
        <path d="M400 600 C330 700 250 800 120 930 H400 Z" fill="var(--orange)"/>
        <path d="M400 690 C320 780 230 860 150 930 H400 Z" fill="var(--orange-dark)" opacity=".55"/>
      </svg>
      <div class="service service--feeding">
        <h2 class="service__title">Feeding Therapy</h2>
        <p class="service__lead">Providing skilled assessment and intervention to children with feeding difficulties.</p>
        <svg class="service__rule" viewBox="0 0 345 14" preserveAspectRatio="none" aria-hidden="true"><path d="M0 12 Q170 -4 345 8" stroke="var(--rule-blue)" stroke-width="4" fill="none"/></svg>
        <ul class="service__list">
          <li>Food Aversions</li>
          <li>Food Refusal</li>
          <li>Very Picky Eating</li>
          <li>Avoidance of Certain Textures</li>
          <li>Gagging and Vomiting</li>
          <li>Oral Motor/ Chewing Difficulties</li>
          <li>Limited Diet/Food Repertoire</li>
        </ul>
      </div>
      <div class="service service--physical">
        <h2 class="service__title">Physical Therapy</h2>
        <p class="service__lead">Helping children move and interact within their environment smoothly and confidently.</p>
        <svg class="service__rule" viewBox="0 0 345 14" preserveAspectRatio="none" aria-hidden="true"><path d="M0 12 Q170 -4 345 8" stroke="var(--rule-blue)" stroke-width="4" fill="none"/></svg>
        <ul class="service__list">
          <li>Torticollis</li>
          <li>Walking and Mobility</li>
          <li>Developmental Motor Milestones</li>
          <li>Balance, Coordination, Motor Planning</li>
          <li>Strength, Muscle Tone and Range of Motion</li>
          <li>Sports Injuries</li>
          <li>Toe Walking</li>
          <li>Myofascial Release</li>
          <li>Postural Control and Positioning</li>
        </ul>
      </div>
      <div class="service service--group">
        <h2 class="service__title">Group Therapy</h2>
        <p class="service__lead">Using peer role models to learn new and challenging skills.</p>
        <svg class="service__rule" viewBox="0 0 345 14" preserveAspectRatio="none" aria-hidden="true"><path d="M0 12 Q170 -4 345 8" stroke="var(--rule-blue)" stroke-width="4" fill="none"/></svg>
        <ul class="service__list">
          <li>Social Groups</li>
          <li>Feeding Groups</li>
        </ul>
      </div>
      <p class="note">**More Group Classes Coming Soon</p>
    </section>
  </main>
</body>
</html>
```